Thornbury Building Company - Card Design

I am looking to use the logo designs that you already did for me to develop a business card. I would like the card to have a black background and be double sided. I want white and green logo and text. I have attached an inspiration photo of a look that I like. I would like to use the Vertical Logo attached to take up the full front side of the card. On the back where I have my name and information, I would like to have the horizontal logo or maybe even just the image of the 'A' and trees without the text. I am open, but I am looking for something clean and simple and I want the green to really pop! Additional files can be found under Design #: 58302946

Target Market(s)

Homeowners

Industry/Entity Type

Construction

Contact Information for Business Card

Name: Marcus Thornbury, Title: Project Manager, Phone: 555.274.8136, Email: thornburybuildingcompany@mailvesta.com, address: 487 Larkspur Ln, Felton, CA 95033, Lic# 2468317

Colors
00AB8E
00BBA5
67D7C9
C6EFE9
E9F9F6

Requirements
Nice to have
• I would like to see the logos that I have already got from ArtLoomHub, though I am open to new ones

```html
<!DOCTYPE html>
<html lang="en">
<head>
<meta charset="UTF-8">
<title>Thornbury Building Company – Business Card</title>
<link rel="stylesheet" href="https://fonts.googleapis.com/css2?family=Montserrat:wght@400;500;700&display=swap">
<style>
  :root {
    --backdrop: #2f2925;
    --card: #1b1b1b;
    --green: #4cb848;
    --white: #f4f4f4;
    --muted: #d8d8d8;
  }
  * { box-sizing: border-box; margin: 0; padding: 0; }
  html, body {
    width: 1200px; height: 786px; overflow: hidden;
    background: var(--backdrop);
    font-family: "Montserrat", sans-serif;
  }
  .canvas {
    position: relative; width: 1200px; height: 786px;
    display: flex; align-items: center; justify-content: center; gap: 40px;
  }
  .card {
    width: 540px; height: 309px;
    background: var(--card);
    border-radius: 4px;
    box-shadow: 0 14px 30px rgba(0,0,0,.45);
    position: relative;
    overflow: hidden;
  }
  /* Back side: contact details */
  .card-back { display: flex; align-items: center; }
  .brand-block {
    width: 250px; padding-left: 34px;
    display: flex; align-items: center; gap: 12px;
  }
  .brand-mark { width: 22px; height: 22px; background: var(--green); flex: none; }
  .brand-name {
    color: var(--white); font-weight: 700; font-size: 19px;
    line-height: 1.15; text-transform: uppercase; letter-spacing: .5px;
  }
  .divider { width: 2px; height: 138px; background: var(--green); margin-right: 22px; }
  .contact { color: var(--white); }
  .contact-name { color: var(--green); font-weight: 700; font-size: 21px; line-height: 1.05; }
  .contact-title { font-size: 12px; color: var(--muted); margin-bottom: 14px; }
  .license { font-size: 12.5px; margin-bottom: 8px; }
  .license .label { color: var(--green); font-weight: 500; }
  .license .number { font-weight: 700; }
  .contact-line { display: flex; align-items: center; gap: 9px; font-size: 11px; margin-top: 5px; white-space: nowrap; }
  .contact-line svg { width: 11px; height: 11px; flex: none; fill: var(--green); }
  .contact-line.email { font-size: 10px; }
  /* Front side: logo only */
  .card-front { display: flex; align-items: center; justify-content: center; gap: 18px; }
  .card-front .brand-mark { width: 40px; height: 40px; }
  .card-front .brand-name { font-size: 32px; line-height: 1.1; }
</style>
</head>
<body>
<main class="canvas">
  <section class="card card-back" aria-label="Business card back">
    <div class="brand-block">
      <span class="brand-mark"></span>
      <span class="brand-name">Thornbury<br>Building<br>Company</span>
    </div>
    <div class="divider"></div>
    <div class="contact">
      <p class="contact-name">Marcus Thornbury</p>
      <p class="contact-title">Project Manager</p>
      <p class="license"><span class="label">Lic</span> <span class="number">#2468317</span></p>
      <p class="contact-line">
        <svg viewBox="0 0 24 24" aria-hidden="true"><path d="M12 1a8 8 0 0 0-8 8c0 6 8 14 8 14s8-8 8-14a8 8 0 0 0-8-8zm0 11a3 3 0 1 1 0-6 3 3 0 0 1 0 6z"/></svg>
        487 Larkspur Ln, Felton, CA 95033
      </p>
      <p class="contact-line">
        <svg viewBox="0 0 24 24" aria-hidden="true"><path d="M6.6 10.8a15 15 0 0 0 6.6 6.6l2.2-2.2a1 1 0 0 1 1-.25 11.4 11.4 0 0 0 3.6.57 1 1 0 0 1 1 1V20a1 1 0 0 1-1 1A17 17 0 0 1 3 4a1 1 0 0 1 1-1h3.5a1 1 0 0 1 1 1c0 1.25.2 2.45.57 3.57a1 1 0 0 1-.25 1z"/></svg>
        555.274.8136
      </p>
      <p class="contact-line email">
        <svg viewBox="0 0 24 24" aria-hidden="true"><path d="M2 5h20v14H2zm2 2v.5l8 5 8-5V7l-8 5z"/></svg>
        thornburybuildingcompany@mailvesta.com
      </p>
    </div>
  </section>

  <section class="card card-front" aria-label="Business card front">
    <span class="brand-mark"></span>
    <span class="brand-name">Thornbury<br>Building Company</span>
  </section>
</main>
</body>
</html>
```